Business Card Design 2018 Kestrel Machining

Hello,

We need a business card design to reflect our new website we just had designed ( http://www.kestrelmachining.ca/)

We are a growing machine shop looking to grow our clientele and are hoping to update our current business card design to match our website and industry

The colours and design of our website should match to achieve what we are looking for.

I have attached a few images for reference as well as our logo and ISO 9000 needs to be apparent on the card as well

Please let me know what you have :)
Please copy marla@kestrelmachining.ca on all communication regarding this project

Thanks !!!

Industry/Entity Type

Business

Contact Information for Business Card

Company Name, employee name and title and contact details

Colors
f78f20
ffffff
00a990

Requirements
Must have
• Our logo, Iso 9000 same colours as our website http://www.kestrelmachining.ca/

```html
<!DOCTYPE html>
<html lang="en">
<head>
<meta charset="utf-8">
<title>Kestrel Machining – Business Card</title>
<link rel="stylesheet" href="https://fonts.googleapis.com/css2?family=Open+Sans:wght@400;600;700;800&display=swap">
<style>
  :root {
    --backdrop: #2e2a27;
    --card: #0d0d0d;
    --ink: #f2f2f2;
    --muted: #bdbdbd;
    --teal: #00a990;
    --rule: #5a5a5a;
    --social: #2f6fc1;
  }
  html, body {
    margin: 0;
    width: 1200px;
    height: 900px;
    overflow: hidden;
    background: var(--backdrop);
    font-family: "Open Sans", Arial, sans-serif;
  }
  .canvas {
    position: relative;
    width: 1200px;
    height: 900px;
  }
  .card {
    position: absolute;
    top: 295px;
    width: 540px;
    height: 310px;
    background: var(--card);
    box-shadow: 0 10px 30px rgba(0,0,0,.45);
    color: var(--ink);
  }
  .card--front { left: 40px; }
  .card--back { left: 620px; }

  /* wordmark */
  .wordmark {
    display: flex;
    align-items: center;
    gap: 8px;
    font-weight: 800;
    text-transform: uppercase;
    color: var(--ink);
    white-space: nowrap;
  }
  .wordmark__mark {
    width: 22px;
    height: 22px;
    background: var(--ink);
    flex: none;
  }
  .card--front .wordmark {
    position: absolute;
    left: 30px;
    top: 146px;
    font-size: 17px;
    letter-spacing: 0;
  }
  .card--back .wordmark {
    position: absolute;
    left: 0;
    right: 0;
    top: 96px;
    justify-content: center;
    font-size: 24px;
    letter-spacing: .5px;
  }
  .card--back .wordmark__mark { width: 30px; height: 30px; }

  /* front details */
  .divider-v {
    position: absolute;
    left: 300px;
    top: 62px;
    width: 1px;
    height: 140px;
    background: var(--rule);
  }
  .contact {
    position: absolute;
    left: 318px;
    top: 46px;
  }
  .contact__name {
    margin: 0;
    font-size: 15px;
    font-weight: 700;
    color: var(--teal);
    letter-spacing: .6px;
    text-transform: uppercase;
  }
  .contact__title {
    margin: 0 0 10px;
    font-size: 12px;
    color: var(--ink);
  }
  .contact__list {
    list-style: none;
    margin: 0;
    padding: 0;
    font-size: 12px;
    line-height: 19px;
  }
  .contact__list li { display: flex; align-items: center; gap: 7px; }
  .contact__icon { width: 10px; height: 10px; flex: none; }
  .contact__address {
    margin: 10px 0 0;
    font-size: 12px;
    line-height: 17px;
    font-style: normal;
  }
  .footer-rule {
    position: absolute;
    left: 170px;
    right: 170px;
    top: 270px;
    height: 1px;
    background: var(--rule);
  }
  .social-badge {
    position: absolute;
    left: 258px;
    top: 258px;
    width: 24px;
    height: 24px;
    background: var(--social);
  }

  /* back */
  .back-rule {
    position: absolute;
    left: 130px;
    right: 130px;
    top: 148px;
    height: 1px;
    background: var(--rule);
  }
  .certification {
    position: absolute;
    left: 0;
    right: 0;
    top: 166px;
    display: flex;
    align-items: center;
    justify-content: center;
    gap: 12px;
  }
  .certification__rule {
    width: 90px;
    height: 1px;
    background: var(--rule);
  }
  .certification__text { text-align: center; line-height: 1; }
  .certification__standard {
    display: block;
    font-size: 24px;
    font-weight: 400;
    letter-spacing: 1px;
  }
  .certification__standard strong { font-weight: 700; }
  .certification__label {
    display: block;
    margin-top: 3px;
    font-size: 7px;
    letter-spacing: 3px;
    color: var(--muted);
  }
</style>
</head>
<body>
<main class="canvas">
  <section class="card card--front" aria-label="Business card front">
    <div class="wordmark"><span class="wordmark__mark"></span>Kestrel Machining</div>
    <div class="divider-v"></div>
    <div class="contact">
      <p class="contact__name">Daniel Reyes</p>
      <p class="contact__title">Managing Director</p>
      <ul class="contact__list">
        <li>
          <svg class="contact__icon" viewBox="0 0 10 10"><path d="M2 1 L4 1 L4.6 3 L3.4 3.8 Q4.4 5.8 6.2 6.6 L7 5.4 L9 6 L9 8 Q5 9.5 1 4 Z" fill="var(--teal)"/></svg>
          780 555 0142
        </li>
        <li>
          <svg class="contact__icon" viewBox="0 0 10 10"><rect x="1" y="3" width="8" height="6" fill="var(--teal)"/><rect x="3" y="1" width="4" height="3" fill="var(--teal)"/></svg>
          888 555 0199
        </li>
        <li>
          <svg class="contact__icon" viewBox="0 0 10 10"><rect x="1" y="2" width="8" height="6" fill="var(--teal)"/><path d="M1 2 L5 5.5 L9 2" stroke="var(--card)" fill="none"/></svg>
          info@kestrelmachining.ca
        </li>
        <li>
          <svg class="contact__icon" viewBox="0 0 10 10"><circle cx="5" cy="5" r="4.5" fill="var(--teal)"/><path d="M3 5 L7 5 M5 3 L7 5 L5 7" stroke="var(--card)" fill="none"/></svg>
          www.kestrelmachining.ca
        </li>
      </ul>
      <address class="contact__address">4120 72 Ave NW<br>Edmonton, AB, T6B 2N4</address>
    </div>
    <div class="footer-rule"></div>
    <div class="social-badge" aria-label="Social profile"></div>
  </section>

  <section class="card card--back" aria-label="Business card back">
    <div class="wordmark"><span class="wordmark__mark"></span>Kestrel Machining</div>
    <div class="back-rule"></div>
    <div class="certification">
      <span class="certification__rule"></span>
      <div class="certification__text">
        <span class="certification__standard">ISO<strong>9001</strong></span>
        <span class="certification__label">CERTIFIED</span>
      </div>
    </div>
  </section>
</main>
</body>
</html>
```